web page look and feel - B2B enterprise application

We have an enterprise application with 10 to 15 core pages and several supporting pages or popups. To start, we want the graphical design of the Users, Roles and Data Source pages and their supporting popups, wizards, etc. to be made beautiful. That is around 10 pages in total. There is a fair amount of redundancy among the pages. I have attached 5 screenshots. We very much want the pages to project a premium feel. That is absolutely essential. The color scheme is blue and sometimes yellow (only if it makes the page look better) plus black, gray and white. If the design of these screens goes well, we would expand the project to continue with other pages. The core of what we are looking for is graphic in nature but we are open to workflow suggestions if you have them. The Roles screen needs some improvements to the layout. I am looking for everything that includes icons, fonts, spacing, etc. I assume getting to the final design will take some back and forth with multiple revisions.

Target Market(s)

Large Enterprises

Number of Pages Required

5+ page

Requirements
Must have
• Premium feel

```html
<!DOCTYPE html>
<html lang="en">
<head>
<meta charset="utf-8">
<title>Users</title>
<link href="https://fonts.googleapis.com/css2?family=Open+Sans:wght@400;600;700&display=swap" rel="stylesheet">
<style>
:root{
  --navy:#1f2839;
  --navy-line:#2d374a;
  --yellow:#f6b91b;
  --ink:#2b2b2b;
  --muted:#6b6f76;
  --head:#4b4f56;
  --sub-head:#a9a9a9;
  --line:#e2e4e8;
  --page:#f4f5f7;
  --white:#fff;
}
*{box-sizing:border-box;margin:0;padding:0}
html,body{width:1200px;height:694px;overflow:hidden}
body{font-family:"Open Sans",Arial,sans-serif;color:var(--ink);background:var(--page);position:relative;font-size:11px}
.sidebar{position:absolute;left:0;top:0;width:169px;height:694px;background:var(--navy);color:#fff}
.brand{position:absolute;left:18px;top:10px;display:flex;align-items:center;gap:7px;font-size:18px;font-weight:600;letter-spacing:-.2px}
.brand .dot{width:14px;height:14px;border-radius:50%;background:var(--yellow)}
.avatar{position:absolute;left:43px;top:75px;width:70px;height:70px;border-radius:50%;background:radial-gradient(circle at 50% 40%,#c79a82,#6b5f5a);border:2px solid #fff}
.avatar-badge{position:absolute;left:93px;top:120px;width:26px;height:26px;border-radius:50%;background:var(--yellow);display:flex;align-items:center;justify-content:center}
.user-name{position:absolute;left:0;width:160px;top:162px;text-align:center;font-size:12px}
.logout{position:absolute;left:0;width:160px;top:179px;text-align:center;font-size:9px;font-weight:700;color:var(--yellow);letter-spacing:.5px}
.nav-item{position:absolute;left:0;width:169px;display:flex;align-items:center;font-size:8.5px;font-weight:700;letter-spacing:.3px;padding-left:12px;gap:10px}
.nav-item svg{flex:none}
.nav-item .chev{position:absolute;right:14px}
.nav-item.active{color:var(--yellow)}
.nav-sep{position:absolute;left:0;width:169px;height:1px;background:var(--navy-line)}
.sub-item{position:absolute;left:36px;font-size:9.5px;display:flex;align-items:center;gap:6px}
.topbar{position:absolute;left:169px;top:0;width:1031px;height:37px;background:#fff;box-shadow:0 1px 3px rgba(0,0,0,.08)}
.burger{position:absolute;left:14px;top:12px}
.top-link{position:absolute;top:0;height:37px;display:flex;align-items:center;gap:6px;font-size:9.5px;border-left:1px solid var(--line);padding:0 0 0 14px}
.top-link.first{border:none;padding:0}
h1{position:absolute;left:194px;top:68px;font-size:20px;font-weight:400}
.search{position:absolute;left:902px;top:64px;width:208px;height:26px;border:1px solid #cfd2d6;background:#fff;font-size:7.5px;color:#555;padding:8px 11px;letter-spacing:.3px}
.search svg{position:absolute;right:8px;top:8px}
.adv{position:absolute;left:1036px;top:95px;font-size:7.5px;color:#555;letter-spacing:.2px}
.add-btn{position:absolute;left:1121px;top:65px;width:61px;height:26px;background:var(--yellow);font-size:10px;font-weight:700;display:flex;align-items:center;justify-content:center;gap:4px;color:#222}
.table{position:absolute;left:194px;top:118px;width:988px;background:#fff}
.row{display:grid;grid-template-columns:36px 175px 173px 182px 241px 81px 100px;align-items:center;border-bottom:1px solid var(--line);font-size:10.5px}
.row>div{padding-left:14px;height:100%;display:flex;align-items:center;border-left:1px solid var(--line)}
.row>div:first-child{border-left:none;justify-content:center;padding:0}
.row .status{justify-content:center;padding:0}
.row.head{background:var(--head);color:#fff;font-size:9.5px;font-weight:700;height:30px;border:none}
.row.head>div{justify-content:center;position:relative;border-left:1px solid #5d6169}
.row.head .sort{position:absolute;right:12px}
.actions{justify-content:center;gap:7px;padding:0!important}
.ic{width:19px;height:19px;border-radius:50%;border:1px solid #9a9ea5;display:flex;align-items:center;justify-content:center;background:#fff}
.ic.on{background:var(--yellow);border-color:var(--yellow)}
.row.hover{box-shadow:0 2px 10px rgba(0,0,0,.12);position:relative}
.perm{border:1px solid #cfd2d6;border-top:none;border-bottom:1px solid #cfd2d6;height:203px;position:relative;background:#fff}
.perm-head{display:grid;grid-template-columns:491px 1fr;background:var(--sub-head);color:#fff;font-weight:700;font-size:10px;height:29px}
.perm-head div{padding-left:21px;display:flex;align-items:center}
.perm-head div+div{border-left:1px solid #fff;padding-left:18px}
.perm-row{display:grid;grid-template-columns:491px 1fr;font-size:10px;border-bottom:1px solid var(--line)}
.perm-row div{padding-left:21px;display:flex;align-items:center}
.perm-row div+div{border-left:1px solid #9a9a9a;padding-left:20px;gap:16px}
.perm-row:last-of-type{border-bottom:none}
.chk{display:flex;align-items:center;gap:5px}
.edit-btn{position:absolute;left:466px;top:169px;width:51px;height:21px;background:var(--yellow);font-size:9px;font-weight:700;display:flex;align-items:center;justify-content:center;gap:4px}
.pager{position:absolute;top:612px;left:0;width:1200px;height:16px}
.pager>span{position:absolute;top:0}
.pg{width:17px;height:15px;border:1px solid #c3c6cb;border-radius:3px;background:#fff;font-size:7px;display:flex;align-items:center;justify-content:center}
.pg.arrow{width:28px;border:none;background:#999}
.pg.arrow.next{background:var(--yellow)}
.pg.size{width:30px;gap:3px}
.dots{font-size:8px;color:#777;line-height:15px}
.footer{position:absolute;left:169px;top:656px;width:1031px;height:38px;background:#fff;border-top:1px solid var(--line);font-size:9px;display:flex;align-items:center;justify-content:center;color:#333}
.footer .ver{position:absolute;right:14px}
</style>
</head>
<body>
<aside class="sidebar">
  <div class="brand"><span class="dot"></span>Norvale Data</div>
  <div class="avatar" role="img" aria-label="User profile photo"></div>
  <div class="avatar-badge"><svg width="14" height="14" viewBox="0 0 14 14"><circle cx="7" cy="7" r="4" fill="none" stroke="#333" stroke-width="1.6"/><circle cx="7" cy="7" r="1.5" fill="#333"/></svg></div>
  <div class="user-name">Dan Harlow</div>
  <div class="logout">LOGOUT</div>

  <div class="nav-item active" style="top:236px;height:18px"><svg width="16" height="14" viewBox="0 0 16 14"><circle cx="7" cy="4" r="3" fill="none" stroke="#f6b91b" stroke-width="1.2"/><path d="M1 13c0-3 3-5 6-5s6 2 6 5z" fill="none" stroke="#f6b91b" stroke-width="1.2"/></svg>USERS
    <svg class="chev" width="16" height="16" viewBox="0 0 16 16"><circle cx="8" cy="8" r="8" fill="#f6b91b"/><path d="M4.5 9.5 8 6l3.5 3.5" fill="none" stroke="#1f2839" stroke-width="1.6"/></svg></div>
  <div class="sub-item" style="top:272px"><svg width="4" height="6"><path d="M0 0l4 3-4 3z" fill="#fff"/></svg>Roles</div>
  <div class="sub-item" style="top:291px"><svg width="4" height="6"><path d="M0 0l4 3-4 3z" fill="#fff"/></svg>Notification Groups</div>
  <div class="nav-sep" style="top:316px"></div>
  <div class="nav-item" style="top:328px;height:16px"><svg width="12" height="14" viewBox="0 0 12 14"><ellipse cx="6" cy="3" rx="5" ry="2" fill="none" stroke="#fff"/><path d="M1 3v8c0 1 2 2 5 2s5-1 5-2V3M1 7c0 1 2 2 5 2s5-1 5-2" fill="none" stroke="#fff"/></svg>DATA SOURCES
    <svg class="chev" width="10" height="6"><path d="M1 1l4 4 4-4" fill="none" stroke="#fff" stroke-width="1.3"/></svg></div>
  <div class="nav-sep" style="top:356px"></div>
  <div class="nav-item" style="top:369px;height:16px"><svg width="12" height="12" viewBox="0 0 12 12" fill="#fff"><rect width="3" height="3"/><rect x="4.5" width="3" height="3"/><rect x="9" width="3" height="3"/><rect y="4.5" width="3" height="3"/><rect x="4.5" y="4.5" width="3" height="3"/><rect x="9" y="4.5" width="3" height="3"/><rect y="9" width="3" height="3"/><rect x="4.5" y="9" width="3" height="3"/><rect x="9" y="9" width="3" height="3"/></svg>DATA SETS</div>
  <div class="nav-sep" style="top:397px"></div>
  <div class="nav-item" style="top:408px;height:16px"><svg width="11" height="14" viewBox="0 0 11 14"><path d="M.5.5h7l3 3v10H.5z M3 6h5M3 8.5h5M3 11h5" fill="none" stroke="#fff"/></svg>RULE SETS</div>
  <div class="nav-sep" style="top:436px"></div>
  <div class="nav-item" style="top:448px;height:16px"><svg width="13" height="13" viewBox="0 0 13 13"><rect x=".5" y="1.5" width="12" height="11" fill="none" stroke="#fff"/><path d="M.5 4.5h12M3 7h2M6 7h2M9 7h2M3 10h2M6 10h2" stroke="#fff"/></svg>SCHEDULES</div>
  <div class="nav-sep" style="top:476px"></div>
  <div class="nav-item" style="top:486px;height:22px;line-height:1.15"><svg width="14" height="13" viewBox="0 0 14 13"><path d="M2 5V2h9l-2-1.5M12 8v3H3l2 1.5" fill="none" stroke="#fff" stroke-width="1.4"/></svg><span>METADATA<br>IMPORT/EXPORT</span>
    <svg class="chev" width="10" height="6"><path d="M1 1l4 4 4-4" fill="none" stroke="#fff" stroke-width="1.3"/></svg></div>
</aside>

<header class="topbar">
  <svg class="burger" width="15" height="12"><path d="M0 1h15M0 6h15M0 11h15" stroke="#333" stroke-width="2"/></svg>
  <div class="top-link first" style="left:811px"><svg width="18" height="12" viewBox="0 0 18 12"><path d="M2 11a7 7 0 1 1 14 0" fill="none" stroke="#333" stroke-width="1.4"/><path d="M9 11l3-5" stroke="#333" stroke-width="1.4"/></svg>Lorem</div>
  <div class="top-link" style="left:879px"><svg width="10" height="14" viewBox="0 0 10 14"><path d="M1.5 4a3.5 3.5 0 1 1 5 3c-1.5.8-1.5 1.5-1.5 3" fill="none" stroke="#333" stroke-width="1.6"/><circle cx="5" cy="12.5" r="1" fill="#333"/></svg>Lorem</div>
  <div class="top-link" style="left:953px"><svg width="15" height="15" viewBox="0 0 15 15"><path d="M1 14l9-9" stroke="#333" stroke-width="1.6"/><path d="M11 1v3M9.5 2.5h3M13.5 6v2M12.5 7h2M6 1v2M5 2h2" stroke="#333"/></svg>Lorem</div>
</header>

<h1>Users</h1>
<div class="search">SEARCH<svg width="9" height="9" viewBox="0 0 9 9"><circle cx="3.7" cy="3.7" r="2.8" fill="none" stroke="#333" stroke-width="1.2"/><path d="M6 6l2.5 2.5" stroke="#333" stroke-width="1.4"/></svg></div>
<div class="adv">ADVANCED SEARCH</div>
<div class="add-btn"><svg width="9" height="9"><path d="M4.5 0v9M0 4.5h9" stroke="#222" stroke-width="2"/></svg>ADD</div>

<section class="table">
  <div class="row head">
    <div></div>
    <div>FIRST NAME<svg class="sort" width="7" height="10"><path d="M3.5 0 7 4H0zM3.5 10 0 6h7z" fill="#fff"/></svg></div>
    <div>LAST NAME<svg class="sort" width="7" height="10"><path d="M3.5 0 7 4H0zM3.5 10 0 6h7z" fill="#fff"/></svg></div>
    <div>USERNAME<svg class="sort" width="7" height="10"><path d="M3.5 0 7 4H0zM3.5 10 0 6h7z" fill="#fff"/></svg></div>
    <div>E MAIL ADDRESS<svg class="sort" width="7" height="10"><path d="M3.5 0 7 4H0zM3.5 10 0 6h7z" fill="#fff"/></svg></div>
    <div style="justify-content:flex-start;padding-left:16px">STATUS<svg class="sort" width="7" height="10" style="right:8px"><path d="M3.5 0 7 4H0zM3.5 10 0 6h7z" fill="#fff"/></svg></div>
    <div></div>
  </div>

  <div class="row" style="height:47px">
    <div><svg width="9" height="6"><path d="M1 1l3.5 3.5L8 1" fill="none" stroke="#333" stroke-width="1.5"/></svg></div>
    <div>Robert</div><div>Fenwick</div><div>robert.fenwick</div><div>robertfenwick@mailbox.test</div><div class="status">Active</div>
    <div class="actions"><span class="ic"><svg width="9" height="9"><path d="M1 2h3M1 2v6h6V5M3 6l5-5" fill="none" stroke="#444"/></svg></span><span class="ic"><svg width="9" height="9"><rect x=".5" y="2.5" width="5" height="6" fill="none" stroke="#444"/><rect x="3.5" y=".5" width="5" height="6" fill="#fff" stroke="#444"/></svg></span><span class="ic"><svg width="8" height="9"><path d="M0 1.5h8M3 .5h2M1 2v7h6V2" fill="none" stroke="#444"/></svg></span></div>
  </div>

  <div class="perm">
    <div class="perm-head"><div>OBJECT</div><div>PERMISSIONS</div></div>
    <div class="perm-row" style="height:38px"><div>System Settings</div><div><span class="chk"><svg width="9" height="9"><circle cx="4.5" cy="4.5" r="4.5" fill="#222"/><path d="M2.3 4.6 4 6.2 6.8 3" fill="none" stroke="#fff" stroke-width="1.2"/></svg>Read</span><span class="chk"><svg width="9" height="9"><circle cx="4.5" cy="4.5" r="4.5" fill="#222"/><path d="M2.3 4.6 4 6.2 6.8 3" fill="none" stroke="#fff" stroke-width="1.2"/></svg>Write</span></div></div>
    <div class="perm-row" style="height:29px"><div>Users</div><div><span class="chk"><svg width="9" height="9"><circle cx="4.5" cy="4.5" r="4.5" fill="#222"/><path d="M2.3 4.6 4 6.2 6.8 3" fill="none" stroke="#fff" stroke-width="1.2"/></svg>Read</span><span class="chk"><svg width="9" height="9"><circle cx="4.5" cy="4.5" r="4.5" fill="#222"/><path d="M2.3 4.6 4 6.2 6.8 3" fill="none" stroke="#fff" stroke-width="1.2"/></svg>Write</span></div></div>
    <div class="perm-row" style="height:32px"><div>Data Source</div><div>Role</div></div>
    <div class="perm-row" style="height:31px"><div>All Data Sources</div><div>System Administrator</div></div>
    <div class="edit-btn"><svg width="9" height="9"><path d="M1 2h3M1 2v6h6V5M3 6l5-5" fill="none" stroke="#222" stroke-width="1.2"/></svg>EDIT</div>
  </div>

  <div class="row" style="height:37px">
    <div><svg width="6" height="9"><path d="M1 1l3.5 3.5L1 8" fill="none" stroke="#333" stroke-width="1.5"/></svg></div>
    <div>Robert</div><div>Fenwick</div><div>robert.fenwick</div><div>robertfenwick@mailbox.test</div><div class="status">Active</div>
    <div class="actions"><span class="ic"><svg width="9" height="9"><path d="M1 2h3M1 2v6h6V5M3 6l5-5" fill="none" stroke="#444"/></svg></span><span class="ic"><svg width="9" height="9"><rect x=".5" y="2.5" width="5" height="6" fill="none" stroke="#444"/><rect x="3.5" y=".5" width="5" height="6" fill="#fff" stroke="#444"/></svg></span><span class="ic"><svg width="8" height="9"><path d="M0 1.5h8M3 .5h2M1 2v7h6V2" fill="none" stroke="#444"/></svg></span></div>
  </div>
  <div class="row hover" style="height:35px">
    <div><svg width="6" height="9"><path d="M1 1l3.5 3.5L1 8" fill="none" stroke="#333" stroke-width="1.5"/></svg></div>
    <div>Zane</div><div>Morrow</div><div>zane</div><div>ZaneEMorrow@brightmail.test</div><div class="status">Active</div>
    <div class="actions"><span class="ic on"><svg width="9" height="9"><path d="M1 2h3M1 2v6h6V5M3 6l5-5" fill="none" stroke="#222"/></svg></span><span class="ic"><svg width="9" height="9"><rect x=".5" y="2.5" width="5" height="6" fill="none" stroke="#444"/><rect x="3.5" y=".5" width="5" height="6" fill="#fff" stroke="#444"/></svg></span><span class="ic"><svg width="8" height="9"><path d="M0 1.5h8M3 .5h2M1 2v7h6V2" fill="none" stroke="#444"/></svg></span></div>
  </div>
  <div class="row" style="height:36px">
    <div><svg width="6" height="9"><path d="M1 1l3.5 3.5L1 8" fill="none" stroke="#333" stroke-width="1.5"/></svg></div>
    <div>Megan</div><div>R. Alcott</div><div>MeganRAlcott</div><div>MeganRAlcott@brightmail.test</div><div class="status">Active</div>
    <div class="actions"><span class="ic"><svg width="9" height="9"><path d="M1 2h3M1 2v6h6V5M3 6l5-5" fill="none" stroke="#444"/></svg></span><span class="ic"><svg width="9" height="9"><rect x=".5" y="2.5" width="5" height="6" fill="none" stroke="#444"/><rect x="3.5" y=".5" width="5" height="6" fill="#fff" stroke="#444"/></svg></span><span class="ic"><svg width="8" height="9"><path d="M0 1.5h8M3 .5h2M1 2v7h6V2" fill="none" stroke="#444"/></svg></span></div>
  </div>
  <div class="row" style="height:36px">
    <div><svg width="6" height="9"><path d="M1 1l3.5 3.5L1 8" fill="none" stroke="#333" stroke-width="1.5"/></svg></div>
    <div>Robert</div><div>Fenwick</div><div>robert.fenwick</div><div>robertfenwick@mailbox.test</div><div class="status">Active</div>
    <div class="actions"><span class="ic"><svg width="9" height="9"><path d="M1 2h3M1 2v6h6V5M3 6l5-5" fill="none" stroke="#444"/></svg></span><span class="ic"><svg width="9" height="9"><rect x=".5" y="2.5" width="5" height="6" fill="none" stroke="#444"/><rect x="3.5" y=".5" width="5" height="6" fill="#fff" stroke="#444"/></svg></span><span class="ic"><svg width="8" height="9"><path d="M0 1.5h8M3 .5h2M1 2v7h6V2" fill="none" stroke="#444"/></svg></span></div>
  </div>
  <div class="row" style="height:40px">
    <div><svg width="6" height="9"><path d="M1 1l3.5 3.5L1 8" fill="none" stroke="#333" stroke-width="1.5"/></svg></div>
    <div>Jason</div><div>A. Gilmore</div><div>Gilmore</div><div>JasonAGilmore@brightmail.test</div><div class="status">Active</div>
    <div class="actions"><span class="ic"><svg width="9" height="9"><path d="M1 2h3M1 2v6h6V5M3 6l5-5" fill="none" stroke="#444"/></svg></span><span class="ic"><svg width="9" height="9"><rect x=".5" y="2.5" width="5" height="6" fill="none" stroke="#444"/><rect x="3.5" y=".5" width="5" height="6" fill="#fff" stroke="#444"/></svg></span><span class="ic"><svg width="8" height="9"><path d="M0 1.5h8M3 .5h2M1 2v7h6V2" fill="none" stroke="#444"/></svg></span></div>
  </div>
</section>

<nav class="pager">
  <span class="pg arrow" style="left:938px"><svg width="14" height="7"><path d="M14 3.5H2M4.5 1 1.5 3.5 4.5 6" fill="none" stroke="#fff" stroke-width="1.6"/></svg></span>
  <span class="pg" style="left:976px">1</span>
  <span class="pg" style="left:998px">2</span>
  <span class="pg" style="left:1019px">3</span>
  <span class="pg" style="left:1041px">4</span>
  <span class="dots" style="left:1064px">.....</span>
  <span class="pg" style="left:1081px">25</span>
  <span class="pg arrow next" style="left:1110px"><svg width="14" height="7"><path d="M0 3.5h12M9.5 1l3 2.5-3 2.5" fill="none" stroke="#fff" stroke-width="1.6"/></svg></span>
  <span class="pg size" style="left:1149px">20<svg width="5" height="3"><path d="M0 0h5L2.5 3z" fill="#333"/></svg></span>
</nav>

<footer class="footer">Copyrights @ 2018 All Rights Reserved<span class="ver">X37</span></footer>
</body>
</html>
```